Professional violinist needs business cards

I am trying to attract the following jobs:
-private violin lessons (primarily classical)
-performance gigs (weddings, birthday parties, funerals, etc.)
-collaborations with other artists (studio recordings, performances)

I want to communicate that I have a very high standard of excellence for my work, but I also love people and celebrations.
Values/style words I like are:
love, joy, peace, fun, beauty, authenticity, excellence, warmth, refined/sleek, free spirited. If that's too confusing, just ignore :)

I will attach my favorite business card template that I could find on Canva. The lines are supposed to be like a music staff, which I think is really cool, but I also don't want it to look too busy. I like the simple black and white--I think it looks sharp--but I also am open to other ideas. I also have seen business cards with pictures included that looked great, so I attached an image that could be used as well.

I am also attaching a file that I made of my initials that could be used as a logo, but I'm not sure if it should be included.

Information on the card:
-My name (18 letters total)
-"violinist"
-phone number, email, website

Thank you!

```html
<!DOCTYPE html>
<html lang="en">
<head>
<meta charset="utf-8">
<title>Marianne Holloway – Violinist Business Card</title>
<link href="https://fonts.googleapis.com/css2?family=Dancing+Script:wght@500&family=Cinzel:wght@500&family=Lato:wght@400&display=swap" rel="stylesheet">
<style>
  :root {
    --backdrop: #2b2b2b;
    --card: #20252a;
    --ivory: #f1ede6;
    --gold: #c9b48c;
    --gold-soft: #b9a47c;
    --silver-light: #e9e9ea;
    --silver-dark: #bdbdc0;
    --photo-dark: #1c1f22;
    --photo-mid: #3a372f;
  }
  * { margin: 0; padding: 0; box-sizing: border-box; }
  html, body {
    width: 1200px; height: 1138px; overflow: hidden;
    background: var(--backdrop);
  }
  .canvas { position: relative; width: 1200px; height: 1138px; }

  .card {
    position: absolute; width: 620px; height: 373px;
    border-radius: 16px; overflow: hidden;
    background: var(--card);
    box-shadow: 0 6px 14px rgba(0,0,0,.45);
  }
  .card--front { left: 274px; top: 186px; }
  .card--back { left: 276px; top: 608px; }

  .clef-decoration {
    position: absolute; left: 0; top: 20px; width: 140px; height: 353px;
    border-radius: 0 70px 70px 0;
    background: linear-gradient(180deg, var(--silver-light), var(--silver-dark));
    opacity: .92;
  }

  .brand-mark {
    position: absolute; border-radius: 50%;
    border: 2px solid var(--gold);
  }
  .card--front .brand-mark { left: 336px; top: 88px; width: 88px; height: 88px; }

  .name {
    position: absolute; white-space: nowrap;
    font-family: "Dancing Script", cursive; font-weight: 500;
    color: var(--ivory); transform: translateX(-50%);
    line-height: 1.2;
  }
  .title {
    position: absolute; display: flex; align-items: center; gap: 14px;
    transform: translateX(-50%); white-space: nowrap;
    font-family: "Cinzel", serif; font-weight: 500;
    color: var(--ivory);
  }
  .title::before, .title::after {
    content: ""; height: 1px; background: var(--gold-soft);
  }

  .card--front .name { left: 384px; top: 200px; font-size: 46px; }
  .card--front .title { left: 384px; top: 252px; font-size: 19px; letter-spacing: 3px; }
  .card--front .title::before, .card--front .title::after { width: 82px; }

  .photo {
    position: absolute; inset: 0;
    background: radial-gradient(ellipse at 55% 50%, var(--photo-mid) 0%, var(--photo-dark) 75%);
  }
  .staff-line {
    position: absolute; left: 0; right: 0; height: 2px; background: var(--gold);
  }
  .staff-line--top-a { top: 21px; }
  .staff-line--top-b { top: 26px; }
  .staff-line--bottom-a { top: 347px; }
  .staff-line--bottom-b { top: 352px; }

  .card--back .brand-mark { left: 102px; top: 92px; width: 80px; height: 80px; }
  .card--back .name { left: 353px; top: 94px; font-size: 41px; }
  .card--back .title { left: 353px; top: 140px; font-size: 15px; letter-spacing: 2px; }
  .card--back .title::before, .card--back .title::after { width: 68px; }

  .contact {
    position: absolute; left: 309px; top: 194px; transform: translateX(-50%);
    list-style: none; text-align: center; white-space: nowrap;
    font-family: "Lato", sans-serif; font-size: 16.5px; line-height: 23.5px;
    color: var(--ivory);
  }
  .contact .accent { color: var(--gold); }
</style>
</head>
<body>
<main class="canvas">
  <section class="card card--front">
    <div class="clef-decoration" role="img" aria-label="Large silver treble clef decoration"></div>
    <span class="brand-mark"></span>
    <h1 class="name">Marianne Holloway</h1>
    <p class="title">VIOLINIST</p>
  </section>

  <section class="card card--back">
    <div class="photo" role="img" aria-label="Dimmed photo of a violinist holding her violin and bow against a stone wall"></div>
    <span class="staff-line staff-line--top-a"></span>
    <span class="staff-line staff-line--top-b"></span>
    <span class="staff-line staff-line--bottom-a"></span>
    <span class="staff-line staff-line--bottom-b"></span>
    <span class="brand-mark"></span>
    <h2 class="name">Marianne Holloway</h2>
    <p class="title">VIOLINIST</p>
    <ul class="contact">
      <li>+1 (202) 555-0148</li>
      <li>Marianne@MarianneHolloway.com</li>
      <li>www.<span class="accent">MarianneHolloway</span>.com</li>
      <li>Linden Falls, VA</li>
    </ul>
  </section>
</main>
</body>
</html>
```